Business Cards for IT Consulting Company (Managed Service Provider)

I am looking to have some business cards printed and would like some designs. We are an IT Consulting company based in Vancouver BC. I would like a nice clean and modern look to the cards. I have uploaded all the versions of my logo so parts can be used as needed. Here is a snippit from our website homepage:

Quillbrook Networks Ltd. is an IT Solutions Partner located in Vancouver BC, Canada. We offer IT solutions and support to customers in the greater Vancouver Area. With expertise in Microsoft platforms, as well as Linux and Mac OSX and over 12 years experience in the IT industry, Quillbrook Networks is dedicated to offering our clients top quality service and products. We take pride in the solutions we offer our customers. The greatest compliment a client can give us is to recommend our services.

Quillbrook Networks Ltd. offers a wide range of IT services from onsite service to remote support and managed service solutions. This allows clients to choose the support path that best suits their company’s needs. Supporting many different sized companies from small to enterprise level over the past 12 years Quillbrook Networks has the experience and expertise needed to ensure things run smoothly. Allowing our clients to focus on doing business.

Revolutionizing the way IT services are delivered.

Quillbrook Networks is dedicated to providing our clients with IT solutions that work and grow with them for years to come. This philosophy helps save money in the long run instead of replacing equipment constantly. Far too often IT solutions are not well thought out and while possibly solving the problem at hand, require replacement due to growth or quality within a very short time frame. Quillbrook Networks takes pride in providing solutions that will last and be able to accommodate growth without the need for replacement.

Industry/Entity Type

Information Technology

Contact Information for Business Card

Quillbrook Networks Ltd.
(Employee Name)
Eml: (Employees Email Address)
Web: quillbrook.me
Ph: 604-555-0148

Font styles to use
Serif
Sans Serif

Requirements
Must have
• The Company logo and company colors.
Nice to have
• - Our tag line: "Revolutionizing IT Services" or "Revolutionizing the way IT services are delivered."
• - Also I really like the idea of nature and technology together blending which is sort of where my logo came from so integrating that somehow onto the business cards would be great.

```html
<!DOCTYPE html>
<html lang="en">
<head>
<meta charset="utf-8">
<title>Quillbrook Networks Ltd. — Business Cards</title>
<link rel="stylesheet" href="https://fonts.googleapis.com/css2?family=Raleway:wght@400;500;600&display=swap">
<style>
  :root {
    --bg: #cfe9e0;
    --card: #050505;
    --blue: #0b9be0;
    --white: #f4f4f4;
    --grey: #8a8a8a;
    --mark-tone: #0d2a38;
  }
  * { margin: 0; padding: 0; box-sizing: border-box; }
  html, body {
    width: 1200px;
    height: 856px;
    overflow: hidden;
    background: var(--bg);
    font-family: "Raleway", sans-serif;
  }
  .canvas {
    position: relative;
    width: 1200px;
    height: 856px;
  }
  .card {
    position: absolute;
    left: 300px;
    width: 600px;
    height: 343px;
    background: var(--card);
    border-radius: 28px;
    overflow: hidden;
  }
  .card--back { top: 60px; }
  .card--front { top: 453px; }

  .wordmark {
    display: flex;
    align-items: center;
    gap: 14px;
    color: var(--blue);
    font-weight: 600;
    white-space: nowrap;
  }
  .wordmark__dot {
    flex: none;
    border-radius: 50%;
    background: var(--blue);
  }

  /* Back */
  .card--back .wordmark {
    position: absolute;
    left: 0;
    right: 0;
    top: 96px;
    justify-content: center;
    font-size: 34px;
    letter-spacing: 0.3px;
  }
  .card--back .wordmark__dot { width: 38px; height: 38px; }
  .tagline {
    position: absolute;
    left: 0;
    right: 0;
    top: 220px;
    text-align: center;
    font-size: 27px;
    font-weight: 400;
    letter-spacing: 1px;
    color: var(--blue);
  }
  .tagline__tail { color: var(--grey); }

  /* Front */
  .brand-decoration {
    position: absolute;
    left: 0;
    top: 0;
    width: 250px;
    height: 343px;
    background: linear-gradient(135deg, var(--mark-tone), var(--card) 80%);
  }
  .front-column {
    position: absolute;
    left: 280px;
    right: 28px;
    top: 0;
    bottom: 0;
  }
  .card--front .wordmark {
    position: absolute;
    left: 0;
    top: 32px;
    font-size: 19px;
    gap: 10px;
  }
  .card--front .wordmark__dot { width: 22px; height: 22px; }
  .person-name {
    position: absolute;
    left: 0;
    top: 104px;
    font-size: 30px;
    font-weight: 400;
    letter-spacing: 1.5px;
    color: var(--blue);
    white-space: nowrap;
  }
  .contact-list {
    position: absolute;
    left: 0;
    top: 170px;
    list-style: none;
  }
  .contact-list__item {
    display: flex;
    align-items: center;
    gap: 12px;
    height: 44px;
    font-size: 17px;
    letter-spacing: 0.3px;
    color: var(--white);
    white-space: nowrap;
  }
  .contact-icon {
    flex: none;
    width: 28px;
    height: 28px;
  }
</style>
</head>
<body>
<main class="canvas">

  <section class="card card--back" aria-label="Card back">
    <div class="wordmark">
      <span class="wordmark__dot"></span>
      <span class="wordmark__name">Quillbrook Networks Ltd.</span>
    </div>
    <p class="tagline">Revolutionizing <span class="tagline__tail">IT Services</span></p>
  </section>

  <section class="card card--front" aria-label="Card front">
    <div class="brand-decoration" role="img" aria-label="Large outlined brand symbol decoration in blue"></div>

    <div class="front-column">
      <div class="wordmark">
        <span class="wordmark__dot"></span>
        <span class="wordmark__name">Quillbrook Networks Ltd.</span>
      </div>

      <h1 class="person-name">DANA WHITLOCK</h1>

      <ul class="contact-list">
        <li class="contact-list__item">
          <svg class="contact-icon" viewBox="0 0 30 30" aria-hidden="true">
            <circle cx="15" cy="15" r="15" fill="#0b9be0"/>
            <rect x="8" y="10" width="14" height="10" rx="1" fill="#fff"/>
            <path d="M8 10 L15 16 L22 10" fill="none" stroke="#0b9be0" stroke-width="1.4"/>
          </svg>
          <span>dana.whitlock@quillbrook.me</span>
        </li>
        <li class="contact-list__item">
          <svg class="contact-icon" viewBox="0 0 30 30" aria-hidden="true">
            <circle cx="15" cy="15" r="15" fill="#0b9be0"/>
            <circle cx="15" cy="15" r="7" fill="none" stroke="#fff" stroke-width="1.5"/>
            <ellipse cx="15" cy="15" rx="3" ry="7" fill="none" stroke="#fff" stroke-width="1.3"/>
            <path d="M8 15 H22 M9.5 11.5 H20.5 M9.5 18.5 H20.5" stroke="#fff" stroke-width="1.2"/>
          </svg>
          <span>quillbrook.me</span>
        </li>
        <li class="contact-list__item">
          <svg class="contact-icon" viewBox="0 0 30 30" aria-hidden="true">
            <circle cx="15" cy="15" r="15" fill="#0b9be0"/>
            <path d="M11 8 C9 9 8.5 11 9.5 13.5 C11 17 13.5 19.5 16.5 21 C19 22 21 21.3 22 19.5 L19.5 17 L17.5 18.3 C15.5 17.3 13 15 12 12.7 L13.3 10.8 Z" fill="#fff"/>
          </svg>
          <span>604-555-0148</span>
        </li>
      </ul>
    </div>
  </section>

</main>
</body>
</html>
```